Oil Field Service company needs professional business cards

Looking to clean up our current company business cards and look a little more professional. Brenwick Casing Services is a US based company that services the oil field. We deal with engineers, managers and oil rigs....................................................................................................................................................................................................................................................................................................................................................................................................

Target Market(s)

Oil and Gas professionals

Industry/Entity Type

Oil And Gas

Contact Information for Business Card

See attached photo as example

Font styles to use
Sans Serif

Colors
ec1f27

Requirements
Must have
• Company Logo, Name, Title, Cell, Office, Fax, Email.
• See attached photo
Nice to have
• External CRT, Internal CRT, Casing Crews, Torque Turn, Laydown Machine
Should not have
• Do not introduce any new pictures and keep it professional looking

```html
<!DOCTYPE html>
<html lang="en">
<head>
<meta charset="utf-8">
<title>Brenwick Casing Services – Business Card</title>
<link href="https://fonts.googleapis.com/css2?family=Open+Sans:wght@400;600;700;800&display=swap" rel="stylesheet">
<style>
  :root {
    --backdrop: #151515;
    --card-white: #ffffff;
    --slate: #44525f;
    --brand-red: #ec1f27;
    --ink: #2b2b2b;
    --light-text: #dde2e7;
  }
  * { margin: 0; padding: 0; box-sizing: border-box; }
  html, body { width: 1200px; height: 900px; overflow: hidden; }
  body {
    background: var(--backdrop);
    font-family: "Open Sans", Arial, sans-serif;
    position: relative;
  }
  .card {
    position: absolute;
    top: 170px;
    width: 347px;
    height: 561px;
    overflow: hidden;
  }
  .card--front { left: 259px; background: var(--card-white); }
  .card--back { left: 631px; background: var(--slate); }

  .card__tab { position: absolute; left: 0; width: 347px; height: 30px; }
  .card__tab--top { top: 0; }
  .card__tab--bottom { bottom: 0; }

  .wordmark {
    position: absolute;
    left: 0; width: 100%;
    text-align: center;
    font-weight: 800;
    line-height: 1;
  }
  .wordmark__name { display: block; font-size: 44px; letter-spacing: 1px; }
  .wordmark__tagline { display: block; font-size: 15px; letter-spacing: 3.5px; margin-top: 12px; }
  .card--front .wordmark { top: 138px; color: var(--slate); }
  .card--back .wordmark { top: 252px; color: var(--card-white); }

  .contact {
    position: absolute;
    top: 324px;
    left: 0; width: 100%;
    text-align: center;
    color: var(--ink);
    font-size: 14.5px;
    line-height: 20px;
  }
  .contact__name {
    color: var(--brand-red);
    font-weight: 700;
    font-size: 20px;
    letter-spacing: 0.3px;
    line-height: 24px;
  }
  .contact__title { margin-bottom: 16px; }
  .contact__label { color: var(--brand-red); font-weight: 700; }
  .contact__address { margin-top: 22px; }

  .services {
    position: absolute;
    top: 424px;
    left: 0; width: 100%;
    list-style: none;
    display: flex;
    flex-wrap: wrap;
    justify-content: center;
    column-gap: 16px;
    row-gap: 7px;
    padding: 0 30px;
    color: var(--light-text);
    font-size: 18px;
    line-height: 22px;
  }
  .services li::before {
    content: "";
    display: inline-block;
    width: 7px; height: 7px;
    border-radius: 50%;
    background: var(--brand-red);
    margin-right: 8px;
    vertical-align: 3px;
  }
</style>
</head>
<body>
  <section class="card card--front">
    <svg class="card__tab card__tab--top" viewBox="0 0 347 30" aria-hidden="true">
      <path d="M102 0 H246 V30 Q174 8 102 30 Z" fill="var(--slate)"/>
    </svg>

    <div class="wordmark">
      <span class="wordmark__name">BRENWICK</span>
      <span class="wordmark__tagline">CASING SERVICES</span>
    </div>

    <div class="contact">
      <p class="contact__name">CODY HARLAN</p>
      <p class="contact__title">Area Manager</p>
      <p><span class="contact__label">P:</span> (555) 214-6800</p>
      <p><span class="contact__label">F:</span> (555) 214-6830 &nbsp;|&nbsp; <span class="contact__label">M:</span> (555) 387-2145</p>
      <p><span class="contact__label">E:</span> codyharlan@brenwickcasing.com</p>
      <p class="contact__address">Ridgefield,&nbsp; OK 73899</p>
    </div>

    <svg class="card__tab card__tab--bottom" viewBox="0 0 347 30" aria-hidden="true">
      <path d="M102 30 H246 V4 Q174 -8 102 4 Z" fill="var(--slate)"/>
    </svg>
  </section>

  <section class="card card--back">
    <div class="wordmark">
      <span class="wordmark__name">BRENWICK</span>
      <span class="wordmark__tagline">CASING SERVICES</span>
    </div>

    <ul class="services">
      <li>External CRT</li>
      <li>Internal CRT</li>
      <li>Casing Crews</li>
      <li>Torque Turn</li>
      <li>Laydown Machine</li>
    </ul>
  </section>
</body>
</html>
```